July 2022 Industrial Manufacturer Product Expo Mexico City

We manufacture large screws and fastners for large Mining equipment, Trains, large ships, airplanes, wind turbines, and so on. We also do custom work base on the customer needs. No matter the size we can make it.
We have a Expo coming up with companies all over the world. We have to stand out we are a family own business so our customer service will be above and beyond anyone can provide. We do not have a sales force to push our products and services we provide one on one service.
Plus@!! I'm looking for anything that you designers can come up with if it was your company to put on a business card, plus i want to do a 1 or 2 sided pamphlet, and then a website. We make Speciality Bolts for large mining equipment these bolts can be 3 to 4 foot long!!! Plus fasteners, Nuts, washers, any, size, strengths, special materials, we offer more of a ono on one customer service, We are a small company, family own, but can fulfill any type of orders. We can also provide special time lines for emergency orders. "We keep the machines running we here at KRV don't believe in down time" We want to hear any slogan based on our company to stand out.
Thanks i really appreciate all your work and options that we have to pick on. Plus just a thought we could possibly want to entertain a experience Marketing internet help maybe a employment possibility. Thanks

I need 2 cards one in Spanish and English Like the steel back ground maybe send me in some bright red and blue writing Same with the Black cards Please remove the word Military The logo KRV maybe integrate a picture of a Bolt 🔩 Thank you

Still looking for I need 2 cards one in Spanish and English Like the steel back ground maybe send me in some bright red and blue writing Same with the Black cards try bright writing Please remove the word Military The logo KRV maybe integrate a picture of a Bolt 🔩 Plus will need the company to make a brochure and website next Thank you

Target Market(s)

Large Mining, Ship, Train, Green Energy, VELM, and Government equipment. Throughout the World

Industry/Entity Type

We can Custom Manufacture any type of Fastners for Mining equipment, Trains, Ships, Green energy, Governments, or military projects. wind turbines,

Contact Information for Business Card

I attached the name and contact info that's on a card, plus the Company Logo. Would like industrial looking background with Bright Colors that will stand out!! If we can insert somewhere maybe on back that we "Custom Manufacture Any Size or Quantity Fastners for Large Mining Equipment, Trains, Ships, Green Energy Equipment or Government Projects

Font styles to use
Other font styles liked:
• You Pick, has to be bold, colorful standout, Professional looking Beable to read it.

Colors

Designer to choose colors to be used in the design.

Requirements
Must have
• Need in Spanish and English TO STANDOUT FROM THE REST OF THE EXPO!! See Business card details, Rounded corners
Nice to have
• Can i see some of the darker cards with Bright Red and Blue letters I like to see the different type of card material, heavy thickness, plastic, transparent, Metal types, Bright Colors, I saw like Raised letters like on the logo.

```html
<!DOCTYPE html>
<html lang="es">
<head>
<meta charset="utf-8">
<title>KRV – Tarjetas de presentación</title>
<link rel="stylesheet" href="https://fonts.googleapis.com/css2?family=Source+Sans+3:wght@600;700&display=swap">
<style>
  :root {
    --backdrop: #2d2d2d;
    --card: #b9b9b9;
    --navy: #14237e;
    --brand-blue: #0a5fb0;
    --red: #e8141b;
    --rule: #777777;
  }
  * { margin: 0; padding: 0; box-sizing: border-box; }
  html, body {
    width: 1093px;
    height: 1200px;
    overflow: hidden;
    background: var(--backdrop);
    font-family: "Source Sans 3", sans-serif;
  }
  .canvas { position: relative; width: 1093px; height: 1200px; }
  .card {
    position: absolute;
    left: 264px;
    width: 580px;
    height: 357px;
    background: var(--card);
    text-align: center;
  }
  .card--front { top: 226px; }
  .card--back { top: 620px; }
  .brand-name {
    position: absolute;
    left: 0; right: 0;
    font-weight: 700;
    font-size: 96px;
    line-height: 1;
    letter-spacing: 6px;
    color: var(--brand-blue);
  }
  .card--front .brand-name { top: 52px; }
  .card--back .brand-name { top: 70px; }
  .holder-name {
    position: absolute; left: 0; right: 0; top: 188px;
    font-weight: 600; font-size: 21px; color: var(--navy);
  }
  .rule {
    position: absolute; left: 50%; width: 74px; margin-left: -37px;
    height: 1px; background: var(--rule);
  }
  .rule--upper { top: 223px; }
  .rule--lower { top: 284px; }
  .quote-line {
    position: absolute; left: 0; right: 0; top: 229px;
    font-weight: 600; font-size: 18.5px; line-height: 24px; color: var(--red);
  }
  .phones {
    position: absolute; left: 0; right: 0; top: 292px;
    display: flex; justify-content: center; gap: 12px;
    font-weight: 600; font-size: 19.5px; color: var(--red);
  }
  .phone { display: flex; align-items: center; gap: 4px; }
  .phone svg { width: 15px; height: 16px; }
  .tagline {
    position: absolute; left: 0; right: 0; top: 223px;
    font-weight: 600; font-size: 19px; line-height: 23.5px; color: var(--red);
  }
</style>
</head>
<body>
<main class="canvas">
  <section class="card card--front" aria-label="Frente de la tarjeta">
    <div class="brand-name">KRV</div>
    <p class="holder-name">Lic. Mariela Sofía Durán Ochoa</p>
    <div class="rule rule--upper"></div>
    <p class="quote-line">Cotizaciones en<br>ventas@krvtornilleria.mx</p>
    <div class="rule rule--lower"></div>
    <div class="phones">
      <span class="phone">
        <svg viewBox="0 0 16 16" aria-hidden="true"><path fill="var(--navy)" d="M3.5 1.5l2.3 2.6-1.2 1.8c.8 1.8 2.2 3.2 4 4l1.8-1.2 2.6 2.3-1.3 2.3C7 13 3 9 1.5 3.7z"/><path fill="none" stroke="var(--navy)" stroke-width="1.3" d="M9.5 2.5a4 4 0 0 1 4 4M9.5 5a1.5 1.5 0 0 1 1.5 1.5"/></svg>
        8712045518
      </span>
      <span class="phone">
        <svg viewBox="0 0 16 16" aria-hidden="true"><rect x="4" y="1" width="8" height="14" rx="1.5" fill="none" stroke="var(--navy)" stroke-width="1.6"/><circle cx="8" cy="12.5" r="1" fill="var(--navy)"/></svg>
        8713306294
      </span>
    </div>
  </section>

  <section class="card card--back" aria-label="Reverso de la tarjeta">
    <div class="brand-name">KRV</div>
    <p class="tagline">Custom Manufacture Any Size or<br>Quantity Fastners for Large&nbsp; Mining<br>Equipment Trains, Ships, Green Energy<br>Equipment or Government Projects</p>
  </section>
</main>
</body>
</html>
```